R7M Horizon Business Card Design

We need a business card created for our New Business "R7M Horizon"<br/><br/>The business card design is up to you however the following information must be on the business card:<br/><br/>Front of the business card -<br/>Email :darrenp@r7mhorizon.nz<br/>Mobile: +64 (0) 22 4870 619<br/>Website: www.r7mhorizon.nz<br/>Card Owner Name: Darren Paltrow<br/>Company Title: Business Development Manager<br/>Slogan: "The BEST of both worlds". <br/>Logo On the front attached to the design brief<br/><br/>On the back: <br/>Space on the back for 4 more versions of the logo across the bottom of the card indicating different subsidiary brands - R7M Coffee, R7M Arts, R7M ?? (The card will be used for all of these brands - We Will add the extra subsidiary logos to the design once the design is finished (We are a graphics design team). <br/><br/>Other than that we want a premium feeling logo that remains universally usable depending on the business entity that we are using the card for. The use of bright bold colours would be great but we still want the card to feel premium.
Target Market(s)
Gift Design and Manufacturing Companies
Contact Information for Business Card
Front of the business card -
Email :darrenp@r7mhorizon.nz
Mobile: +64 (0) 22 4870 619
Website: www.r7mhorizon.nz
Card Owner Name: Darren Paltrow
Company Title: Business Development Manager
Slogan: "The BEST of both worlds".
Logo On the front attached to the design brief

```html
<!DOCTYPE html>
<html lang="en">
<head>
<meta charset="utf-8">
<title>R7M Horizon – Business Card</title>
<link rel="stylesheet" href="https://fonts.googleapis.com/css2?family=Montserrat:wght@700;800&family=Arimo:wght@400&display=swap">
<style>
  :root {
    --brand-blue: #2f3fa0;
    --ink: #2a2a2a;
    --rule: #bdbdbd;
    --card-white: #ffffff;
    --card-soft: #f7f7f7;
    --backdrop: #e4e4e6;
  }
  * { box-sizing: border-box; margin: 0; padding: 0; }
  html, body {
    width: 1200px; height: 900px; overflow: hidden;
    background: var(--backdrop);
  }
  .canvas {
    position: relative; width: 1200px; height: 900px;
  }
  .card {
    position: absolute; left: 340px; width: 520px; height: 300px;
    background: var(--card-white);
    border-bottom: 10px solid var(--brand-blue);
    overflow: hidden;
    box-shadow: 0 6px 18px rgba(0,0,0,0.12);
  }
  .card--logo { top: 110px; background: var(--card-soft); }
  .card--info { top: 490px; }

  /* Logo side */
  .brand-name {
    position: absolute; left: 50%; top: 50%;
    transform: translate(-50%, -50%);
    font-family: 'Montserrat', sans-serif; font-weight: 800;
    font-size: 40px; color: var(--brand-blue); letter-spacing: 0.5px;
    white-space: nowrap;
  }

  /* Info side */
  .contact-block {
    position: absolute; left: 0; right: 0; top: 44px;
    display: flex; flex-direction: column; align-items: center;
    text-align: center;
  }
  .holder-name {
    font-family: 'Montserrat', sans-serif; font-weight: 800;
    font-size: 17px; color: var(--brand-blue); letter-spacing: 0.6px;
    text-transform: uppercase;
  }
  .holder-title {
    font-family: 'Arimo', sans-serif; font-size: 14px; color: var(--ink);
    margin-top: 2px;
  }
  .divider {
    position: relative; width: 180px; height: 1px; background: var(--rule);
    margin: 14px 0 16px;
  }
  .divider--icons { margin: 16px 0 12px; }
  .icon-row {
    position: absolute; left: 50%; top: 50%;
    transform: translate(-50%, -50%);
    display: flex; gap: 5px; background: var(--card-white); padding: 0 6px;
  }
  .icon-tile {
    width: 18px; height: 18px; background: var(--brand-blue); border-radius: 2px;
    display: flex; align-items: center; justify-content: center;
  }
  .contact-lines {
    font-family: 'Arimo', sans-serif; font-size: 14px; line-height: 19px;
    color: var(--ink);
  }
  .slogan {
    font-family: 'Montserrat', sans-serif; font-weight: 800;
    font-size: 14px; color: var(--brand-blue); text-transform: uppercase;
    letter-spacing: 0.3px;
  }
</style>
</head>
<body>
<main class="canvas">

  <section class="card card--logo" aria-label="Card logo side">
    <span class="brand-name">R7M Horizon</span>
  </section>

  <section class="card card--info" aria-label="Card contact side">
    <div class="contact-block">
      <h1 class="holder-name">Darren Paltrow</h1>
      <p class="holder-title">Business Development Manager</p>
      <div class="divider divider--icons">
        <div class="icon-row">
          <span class="icon-tile" aria-label="Phone">
            <svg width="12" height="12" viewBox="0 0 24 24"><path fill="#fff" d="M6.6 10.8a15 15 0 0 0 6.6 6.6l2.2-2.2a1 1 0 0 1 1-.25 11.4 11.4 0 0 0 3.6.57 1 1 0 0 1 1 1V20a1 1 0 0 1-1 1A17 17 0 0 1 3 4a1 1 0 0 1 1-1h3.5a1 1 0 0 1 1 1c0 1.25.2 2.45.57 3.57a1 1 0 0 1-.25 1z"/></svg>
          </span>
          <span class="icon-tile" aria-label="Email">
            <svg width="12" height="12" viewBox="0 0 24 24"><rect x="2" y="5" width="20" height="14" fill="#fff"/><path d="M2 5l10 8 10-8" fill="none" stroke="#2f3fa0" stroke-width="2"/></svg>
          </span>
          <span class="icon-tile" aria-label="Website">
            <svg width="12" height="12" viewBox="0 0 24 24" fill="none" stroke="#fff" stroke-width="2"><circle cx="12" cy="12" r="9"/><path d="M3 12h18M12 3c3 3 3 15 0 18M12 3c-3 3-3 15 0 18"/></svg>
          </span>
        </div>
      </div>
      <p class="contact-lines">
        +64 (0) 22 4870 619<br>
        darrenp@r7mhorizon.nz<br>
        www.r7mhorizon.nz
      </p>
      <div class="divider"></div>
      <p class="slogan">The Best of Both Worlds</p>
    </div>
  </section>

</main>
</body>
</html>
```